Modern card design needed for building development company

We are looking for a sharp modern new look for our business cards.
We are a New Zealand based company called TKR Ventures NZ LTD that specialises in subdividing large sections, housing and commercial buildings.
We have attached a photo of the current logo and would like to see it improved somehow as it looks a bit dated.
We are open to any colours.

Target Market(s)

Investors, Property buyers

Industry/Entity Type

Investment

Contact Information for Business Card

TKR VENTURES NZ LTD
www.tkrventuresnz.co.nz

Damon Whitcombe
Phone +64 21 938 104
Email dpwhitcombe@korumail.co.nz

Font styles to use
Serif
Sans Serif

Colors
0792cd
33a6d7
85cae6
6b449b
886aae
f04a50
ec1f27
f37122
f68d4d

Requirements
Must have
• Please try and make the logo more modern or if you have a similar one we would like to see it.

```html
<!DOCTYPE html>
<html lang="en">
<head>
<meta charset="utf-8">
<title>TKR Ventures NZ LTD – Business Card</title>
<link rel="stylesheet" href="https://fonts.googleapis.com/css2?family=Cinzel:wght@400&family=Open+Sans:wght@400;700&display=swap">
<style>
  :root {
    --stage: #000000;
    --card-back: #999999;
    --card-front: #ffffff;
    --ink-light: #ffffff;
    --ink-dark: #333333;
    --rule-light: #d4d4d4;
    --accent: #0792cd;
  }
  * { margin: 0; padding: 0; box-sizing: border-box; }
  html, body {
    width: 1200px; height: 900px; overflow: hidden;
    background: var(--stage);
  }
  .stage { position: relative; width: 1200px; height: 900px; }

  .card { position: absolute; width: 477px; height: 293px; }
  .card--back {
    left: 116px; top: 275px;
    background: var(--card-back);
    border-radius: 0 46px 0 46px;
  }
  .card--front {
    left: 622px; top: 276px;
    background: var(--card-front);
    border-radius: 46px 0 46px 0;
  }

  .wordmark {
    position: absolute;
    display: flex; align-items: center; gap: 10px;
    font-family: "Cinzel", Georgia, serif;
    font-weight: 400;
    color: var(--ink-dark);
    white-space: nowrap;
  }
  .wordmark__square { background: var(--accent); flex: none; }
  .card--back .wordmark {
    right: 30px; top: 362px; top: 87px;
    font-size: 16px;
  }
  .card--back .wordmark__square { width: 14px; height: 14px; }
  .card--front .wordmark {
    left: 0; right: 0; top: 125px; justify-content: center;
    font-size: 25px;
  }
  .card--front .wordmark__square { width: 22px; height: 22px; }

  .holder-name {
    position: absolute; left: 35px; top: 154px;
    font-family: "Open Sans", Arial, sans-serif;
    font-weight: 700; font-size: 16.5px;
    color: var(--ink-light); letter-spacing: 0.1px;
  }
  .holder-rule {
    position: absolute; left: 37px; top: 181px;
    width: 410px; height: 1px; background: var(--rule-light);
  }
  .contact-list {
    position: absolute; right: 26px; top: 204px;
    list-style: none;
    font-family: "Open Sans", Arial, sans-serif;
    font-size: 14px; line-height: 18px;
    color: var(--ink-light); text-align: right;
  }
  .contact-list li { display: flex; justify-content: flex-end; align-items: center; gap: 8px; }
  .contact-list svg { width: 9px; height: 9px; flex: none; }
</style>
</head>
<body>
<main class="stage">
  <section class="card card--back">
    <div class="wordmark"><span class="wordmark__square"></span>TKR Ventures NZ LTD</div>
    <p class="holder-name">DAMON WHITCOMBE</p>
    <div class="holder-rule"></div>
    <ul class="contact-list">
      <li>+64 21 938 104
        <svg viewBox="0 0 9 9" aria-hidden="true"><rect x="2" y="0.5" width="5" height="8" rx="1" fill="none" stroke="#fff" stroke-width="1"/><rect x="3.5" y="6.5" width="2" height="1" fill="#fff"/></svg>
      </li>
      <li>dpwhitcombe@korumail.co.nz
        <svg viewBox="0 0 9 9" aria-hidden="true"><rect x="0.5" y="2" width="8" height="5.5" fill="#fff"/><path d="M0.5 2 L4.5 5 L8.5 2" fill="none" stroke="#999" stroke-width="0.8"/></svg>
      </li>
      <li>www.tkrventuresnz.co.nz
        <svg viewBox="0 0 9 9" aria-hidden="true"><circle cx="4.5" cy="4.5" r="4.2" fill="#fff"/><path d="M2 3.5 L4 3 L5 5 L3.5 6.5 Z M6 2 L7.5 3.5 L6.5 5 Z" fill="#999"/></svg>
      </li>
    </ul>
  </section>

  <section class="card card--front">
    <div class="wordmark"><span class="wordmark__square"></span>TKR Ventures NZ LTD</div>
  </section>
</main>
</body>
</html>
```